New York City Sponsorship Page with Click Through Supporting Pages

Metro Talent Circle, the leading New York City resource for HR Professionals is a membership organization with almost 2,000 individual members.

We need section/page(s) created for our current sponsorship offerings. Our platform is on ClubLedger Platform and we need capability to edit the page, etc. It must be HTML ready/coded.

Attached is the mock up of how we want the page to look (pages mockup pdf) as well as each of the categories which should be included (in the excel files). Our current page is here: http://www.metrotalentcircle.example/?page=sponsors and is not easy to read through. We want something that is visually appealing and clean but showcases all of the different ways to sponsor the Chapter.

Additionally, we are taking the information from this page and turning it into a brochure.

Target Market(s)

New York City Companies who have HR Professionals or services they want to attract or offer.

Coding

Coded - Design and coding required

Number of Pages Required

5+ page

Requirements
Must have
• Clean Look and feel, easy functionality, necessary information and purchases. Match the top navigation of current page. Opportunity for current sponsor logos to be highlighted on the page. Easy to update/maintain.
Nice to have
• Option to pay for sponsorships through the page using our credit card processor.
Should not have
• Overwhelming text in sections

```html
<!DOCTYPE html>
<html lang="en">
<head>
<meta charset="utf-8">
<title>Sponsorship Opportunities – Metro Talent Circle</title>
<link href="https://fonts.googleapis.com/css2?family=Nunito+Sans:wght@400;700;800&family=Open+Sans:wght@400;600;700&family=Roboto+Condensed:wght@400&family=Roboto:wght@300;400&display=swap" rel="stylesheet">
<style>
:root{
  --navy:#0d2a4a;
  --footer:#0b2847;
  --red:#a31c1c;
  --link:#2a6fb5;
  --gold:#d4ae35;
  --silver:#9a9a9a;
  --bronze:#d9996a;
  --frame:#e6e6e6;
  --soft:#f4f4f4;
  --text:#333;
  --rule:#c9c9c9;
}
*{box-sizing:border-box;margin:0;padding:0}
html,body{width:800px;height:1200px;overflow:hidden}
body{position:relative;background:var(--frame);font-family:"Open Sans",sans-serif;color:var(--text)}
.abs{position:absolute}
.topbar{left:10px;top:10px;width:780px;height:20px;background:var(--navy)}
.toplinks{right:218px;top:5px;font:700 7px "Open Sans",sans-serif;color:#fff;letter-spacing:.1px;display:flex;gap:9px}
.search{left:555px;top:13px;width:93px;height:13px;background:#fff;font-size:6px;color:#999;padding:3px 4px;border-radius:1px}
.sq{width:12px;height:12px;background:#2a8fd6;border-radius:1px}
.header{left:10px;top:30px;width:780px;height:49px;background:linear-gradient(#f7f7f7,#ececec)}
.brand{left:64px;top:44px;display:flex;align-items:center;gap:5px;font:700 13px "Roboto Condensed",sans-serif;color:var(--red)}
.brand .dot{width:14px;height:14px;border-radius:50%;background:var(--navy)}
.nav{left:263px;top:48px;display:flex;gap:19px;font:400 10.5px "Roboto Condensed",sans-serif;color:var(--link)}
.hero{left:10px;top:79px;width:780px;height:90px;background:linear-gradient(180deg,#1c2330 0%,#3a3a32 55%,#14161c 100%)}
.crumb{left:32px;top:177px;font:700 6.5px "Open Sans",sans-serif;color:var(--navy)}
.share{right:30px;top:176px;font:700 6.5px "Open Sans",sans-serif;color:var(--navy);display:flex;align-items:center;gap:4px}
.white1{left:10px;top:169px;width:780px;height:145px;background:#fff;z-index:-1}
.title{left:10px;width:780px;display:flex;justify-content:center;align-items:center;gap:12px;font-family:"Nunito Sans",sans-serif;font-weight:800;color:var(--navy)}
.title::before,.title::after{content:"";width:62px;height:1px;background:var(--rule)}
.title em{font-style:normal;color:var(--red)}
.intro{left:10px;top:264px;width:780px;text-align:center;font:600 8px "Open Sans",sans-serif;color:#333}
.gray{left:10px;width:780px;background:var(--soft)}
.tiers{left:146px;top:419px;width:507px;height:42px;display:flex;border-radius:4px;overflow:hidden;box-shadow:0 1px 2px rgba(0,0,0,.2)}
.tiers div{flex:1;display:flex;align-items:center;justify-content:center;padding-left:14px;color:#fff;font:700 10px "Open Sans",sans-serif}
.tier-circle{width:51px;height:51px;border-radius:50%;border:3px solid #fff;box-shadow:0 1px 2px rgba(0,0,0,.25);display:flex;align-items:center;justify-content:center}
.tier-circle span{width:18px;height:18px;border-radius:50%;border:2px solid #fff}
.band{left:10px;top:498px;width:780px;height:136px;background:linear-gradient(180deg,#3a5573 0%,#27415f 55%,#1e3654 100%)}
.pill{top:549px;width:165px;height:33px;background:#fff;border-radius:3px;display:flex;align-items:center;justify-content:center;padding-left:24px;text-align:center;font:700 9px/1.25 "Open Sans",sans-serif;color:#222}
.ring{width:60px;height:60px;border-radius:50%;background:#fff;border:3px solid var(--navy);outline:2px solid #fff;display:flex;align-items:center;justify-content:center}
.sponsors{left:10px;top:634px;width:780px;height:190px;background:#fff}
.tierlabel{font:700 11px "Open Sans",sans-serif;color:#333}
.mark{font-family:"Open Sans",sans-serif;font-weight:600;font-size:18px}
.dates{display:flex;gap:0}
.datebox{width:46px;height:56px;box-shadow:1px 1px 3px rgba(0,0,0,.3);text-align:center}
.datebox .top{background:var(--navy);color:#fff;height:38px;padding-top:3px}
.datebox .d{font:700 16px/1 "Open Sans",sans-serif}
.datebox .m{font:700 8px/1.3 "Open Sans",sans-serif}
.datebox .y{background:#fff;font:700 9px/18px "Open Sans",sans-serif;color:#333}
.event{width:150px;font:400 7.6px/1.5 "Open Sans",sans-serif;color:#444}
.event b{display:block;color:#333;font-weight:700}
.footer{left:10px;top:1006px;width:780px;height:184px;background:var(--footer);color:#fff}
.fhead{font:300 13px "Roboto",sans-serif;color:#fff}
.flist{font:400 7.6px/14px "Roboto",sans-serif;color:#e4e9ef;list-style:none}
.badge{left:345px;top:1028px;width:135px;height:98px;background:#fff;display:flex;align-items:center;justify-content:center}
.badge span{width:105px;height:64px;background:#6e8fc4;border-radius:2px}
.social{display:flex;gap:7px}
.social span{width:21px;height:21px;background:#2a8fd6;border-radius:1px}
.legal{left:10px;top:1168px;width:780px;text-align:center;font:400 6.5px "Open Sans",sans-serif;color:#fff}
</style>
</head>
<body>
<!-- top utility bar -->
<div class="abs topbar"></div>
<div class="abs toplinks"><span>CONTACT US</span><span>SIGN IN</span><span>JOIN/RENEW</span></div>
<div class="abs search">Enter search criteria...</div>
<div class="abs" style="left:653px;top:13px;display:flex;gap:6px"><span class="sq"></span><span class="sq"></span><span class="sq"></span><span class="sq"></span><span class="sq"></span></div>

<!-- header -->
<div class="abs header"></div>
<div class="abs brand"><span class="dot"></span>Metro Talent Circle</div>
<nav class="abs nav"><span>Our New Website</span><span>About Us</span><span>Membership</span><span>Events</span><span>Sponsorships</span><span>Career Center</span><span>HR Resources</span></nav>
<div class="abs hero" role="img" aria-label="Night skyline of Manhattan with lit office towers"></div>

<!-- intro -->
<div class="abs white1"></div>
<div class="abs crumb">SPONSORSHIPS &nbsp;&gt;&nbsp; SPONSORSHIP OPPORTUNITIES</div>
<div class="abs share">SHARE
  <svg width="12" height="12" viewBox="0 0 12 12"><circle cx="9.5" cy="2.5" r="2" fill="#111"/><circle cx="2.5" cy="6" r="2" fill="#111"/><circle cx="9.5" cy="9.5" r="2" fill="#111"/><path d="M2.5 6 9.5 2.5M2.5 6 9.5 9.5" stroke="#111" stroke-width="1.2"/></svg>
</div>
<h1 class="abs title" style="top:214px;font-size:16px">INVITATION FOR&nbsp;<em>STRATEGIC PARTNERS</em></h1>
<p class="abs intro">Thank you for your interest in our strategic partnership.</p>

<!-- packages -->
<div class="abs gray" style="top:314px;height:184px"></div>
<h2 class="abs title" style="top:351px;font-size:13.5px;gap:14px">Choose the sponsorship package&nbsp;<em>that best meets your needs:</em></h2>
<div class="abs tiers">
  <div style="background:var(--gold)">Gold</div>
  <div style="background:var(--silver)">Silver</div>
  <div style="background:var(--bronze)">Bronze</div>
</div>
<div class="abs tier-circle" style="left:136px;top:403px;background:var(--gold)"><span></span></div>
<div class="abs tier-circle" style="left:304px;top:403px;background:var(--silver)"><span></span></div>
<div class="abs tier-circle" style="left:474px;top:403px;background:var(--bronze)"><span></span></div>

<!-- actions -->
<div class="abs band" role="img" aria-label="Dusk view over the city with skyscrapers"></div>
<div class="abs pill" style="left:120px">More about our<br>sponsorship packages</div>
<div class="abs ring" style="left:92px;top:536px">
  <svg width="32" height="26" viewBox="0 0 32 26"><rect x="2" y="3" width="26" height="18" rx="2" fill="none" stroke="var(--navy)" stroke-width="2.4"/><path d="M2 4 15 14 28 4" fill="none" stroke="var(--navy)" stroke-width="2.4"/></svg>
</div>
<div class="abs pill" style="left:332px">Book your<br>sponsorship packages</div>
<div class="abs ring" style="left:304px;top:536px">
  <svg width="30" height="30" viewBox="0 0 30 30"><circle cx="14" cy="16" r="11" fill="none" stroke="#2a8fd6" stroke-width="2.6"/><circle cx="14" cy="16" r="5.5" fill="none" stroke="#2a8fd6" stroke-width="2.6"/><path d="M14 16 26 4M21 4h5v5" fill="none" stroke="var(--navy)" stroke-width="2.4"/></svg>
</div>
<div class="abs pill" style="left:544px">Contact our<br>sponsorship team</div>
<div class="abs ring" style="left:516px;top:536px">
  <svg width="30" height="30" viewBox="0 0 30 30"><path d="M7 4l5 6-3 3c2 4 5 7 9 9l3-3 6 5-3 4C14 27 3 16 3 7z" fill="none" stroke="var(--red)" stroke-width="2.2" stroke-linejoin="round"/><path d="M17 7a6 6 0 0 1 6 6M17 2a11 11 0 0 1 11 11" fill="none" stroke="var(--red)" stroke-width="2"/></svg>
</div>

<!-- sponsors -->
<div class="abs sponsors"></div>
<h2 class="abs title" style="top:671px;font-size:13.5px;gap:14px">Thanks to&nbsp;<em>our sponsors</em></h2>
<div class="abs tierlabel" style="left:88px;top:720px">Gold</div>
<div class="abs mark" style="left:86px;top:752px;color:#1d3f7a">Harlow Legal</div>
<div class="abs mark" style="left:236px;top:752px;color:#26246a">Transit Perks</div>
<div class="abs tierlabel" style="left:420px;top:720px">Silver</div>
<div class="abs mark" style="left:418px;top:752px;color:#222">Beacon Benefits</div>
<div class="abs mark" style="left:590px;top:752px;color:#2878c0">Staffwell</div>

<!-- calendar -->
<div class="abs gray" style="top:824px;height:182px"></div>
<h2 class="abs title" style="top:861px;font-size:13.5px;gap:14px">Calendar</h2>
<div class="abs datebox" style="left:66px;top:910px"><div class="top"><div class="d">01</div><div class="m">SEP</div></div><div class="y">2016</div></div>
<p class="abs event" style="left:125px;top:910px"><b>Nam liber tempor cum soluta nobis</b>Lorem ipsum dolor sit amet, consecte tuer adipiscing elit, sed diam nonum my nibh euismod tincidunt ut laoreet dolore magna aliquam erat.</p>
<div class="abs datebox" style="left:298px;top:910px"><div class="top"><div class="d">24</div><div class="m">AUG</div></div><div class="y">2016</div></div>
<p class="abs event" style="left:359px;top:910px"><b>Nam liber tempor cum soluta nobis</b>Lorem ipsum dolor sit amet, consecte tuer adipiscing elit, sed diam nonum my nibh euismod tincidunt ut laoreet dolore magna aliquam erat.</p>
<div class="abs datebox" style="left:532px;top:910px"><div class="top"><div class="d">01</div><div class="m">AUG</div></div><div class="y">2016</div></div>
<p class="abs event" style="left:593px;top:910px"><b>Nam liber tempor cum soluta nobis</b>Lorem ipsum dolor sit amet, consecte tuer adipiscing elit, sed diam nonum my nibh euismod tincidunt ut laoreet dolore magna aliquam erat.</p>

<!-- footer -->
<footer class="abs footer"></footer>
<div class="abs" style="left:88px;top:1026px"><div class="fhead">Navigation</div>
  <ul class="flist" style="margin-top:3px"><li>About Us</li><li>Membership</li><li>Events</li><li>Career Center</li><li>Sponsorships</li><li>HR Resources</li></ul></div>
<div class="abs" style="left:208px;top:1026px"><div class="fhead">Contact Us</div>
  <ul class="flist" style="margin-top:3px;line-height:20px"><li>Phone: 800-555-0142</li><li>Fax: 800-555-0187</li><li>hello@metrotalentcircle.example</li></ul></div>
<div class="abs badge"><span></span></div>
<div class="abs" style="left:534px;top:1026px"><div class="fhead">Connect With Us</div>
  <div class="social" style="margin-top:7px"><span></span><span></span><span></span><span></span><span></span></div></div>
<div class="abs legal">Membership Software Powered by ClubLedger.com® &nbsp;::&nbsp; Legal</div>
</body>
</html>
```